Pup Snack Den - New Website Design

Create a professional Storvana website for a the hottest trend; a Pup Snack Den subscription box business. Storvana.com is an easy to use website builder.
Please see frellonbox.com; gummotrove.com and wagcrate.com for the concept I am after. The business has not been launched yet, I am currently in the pre-launch stage using a specialized landing page website, and so the time scale for developing my professional looking Storvana website is up to 1-2 weeks.
The webpage should have a fun feel and should match the style of the company logo at gummotrove.com. The pages to include are 'Home', 'About us' and 'Get Started'
Thank you and good luck!

```html
<!DOCTYPE html>
<html lang="en">
<head>
<meta charset="utf-8">
<title>Pup Snack Den</title>
<link href="https://fonts.googleapis.com/css2?family=Open+Sans:ital,wght@0,400;0,600;0,700;1,400&family=Roboto+Condensed:wght@400;700&display=swap" rel="stylesheet">
<style>
:root{
  --blue:#5aa6dc;
  --blue-dark:#3f8fca;
  --ink:#2b2b2b;
  --muted:#666;
  --white:#fff;
  --footer:#f4f4f4;
  --line:#e2e2e2;
}
*{box-sizing:border-box;margin:0;padding:0}
html,body{width:1200px;height:3279px;overflow:hidden}
body{font-family:"Open Sans",sans-serif;color:var(--ink);background:var(--white);position:relative}
.abs{position:absolute}
.heading{font-family:"Roboto Condensed",sans-serif;text-transform:uppercase}

/* top bar */
.topbar{position:absolute;left:0;top:0;width:1200px;height:30px;background:var(--blue);color:var(--white);font-size:11px;font-weight:600;text-transform:uppercase}
.topbar .promo{position:absolute;left:98px;top:7px}
.topbar .account{position:absolute;right:98px;top:7px;display:flex;gap:34px}
.topbar .account span{display:flex;align-items:center;gap:7px}
.topbar svg{width:12px;height:12px;fill:var(--white)}

/* header */
.site-header{position:absolute;top:30px;left:0;width:1200px;height:106px}
.brand{position:absolute;left:98px;top:30px;display:flex;align-items:center;gap:12px;font-family:"Roboto Condensed",sans-serif;font-size:38px;font-weight:700;color:var(--ink)}
.brand .dot{width:40px;height:40px;border-radius:50%;background:var(--blue)}
.main-nav{position:absolute;right:98px;top:46px;display:flex;gap:26px;font-size:13px;text-transform:uppercase}

/* hero */
.hero{position:absolute;top:136px;left:0;width:1200px;height:515px;background:linear-gradient(100deg,#d9c9b6 0%,#cdb597 40%,#b78a55 65%,#8a6038 100%)}
.sale-badge{position:absolute;left:110px;top:94px;width:300px;height:300px;border-radius:50%;background:var(--blue);color:var(--white);text-align:center;padding-top:72px}
.sale-badge .kicker{font-family:"Roboto Condensed",sans-serif;font-size:19px;font-weight:700}
.sale-badge .big{font-family:"Roboto Condensed",sans-serif;font-size:62px;font-weight:700;line-height:1.05}
.sale-badge .sub{font-family:"Roboto Condensed",sans-serif;font-size:19px;font-weight:700}
.slider-dots{display:flex;gap:6px;justify-content:center;margin-top:16px}
.slider-dots i{width:10px;height:10px;border-radius:50%;background:rgba(255,255,255,.6)}
.slider-dots i.on{background:var(--white)}

/* category tiles */
.tile{position:absolute;top:713px;width:326px;height:240px}
.tile .label{position:absolute;left:50%;top:108px;transform:translateX(-50%);background:rgba(30,30,30,.82);color:var(--white);font-family:"Roboto Condensed",sans-serif;font-size:16px;text-transform:uppercase;padding:7px 24px;white-space:nowrap}

/* subscription band */
.subscribe-band{position:absolute;top:1016px;left:0;width:1200px;height:444px;background:linear-gradient(180deg,#7a5a3c 0%,#5c4029 55%,#6b5444 100%);color:var(--white);text-align:center}
.subscribe-band h2{position:absolute;top:120px;width:100%;font-size:42px;font-weight:700}
.subscribe-band p{position:absolute;top:184px;left:300px;width:600px;font-size:12px;line-height:22px}
.sub-form{position:absolute;left:339px;top:263px;width:522px;height:38px;display:flex}
.sub-form .field{flex:1;background:var(--white);border-radius:19px 0 0 19px;color:var(--ink);font-size:11px;text-align:left;padding:11px 20px}
.sub-form .btn{width:135px;background:var(--blue);border-radius:0 19px 19px 0;font-size:13px;padding-top:10px;text-transform:uppercase}
.gift-box{position:absolute;left:940px;top:220px;width:165px;height:224px;background:linear-gradient(160deg,#d6b285,#b88d5c);border-radius:4px}

/* featured products */
.section-title{position:absolute;width:100%;text-align:center;font-size:30px;font-weight:400}
.product{position:absolute;top:1633px;width:234px;text-align:center}
.product .shot{height:240px}
.product p{font-size:12px;line-height:21px;color:var(--muted);margin-top:18px;padding:0 18px}
.product .price{font-style:italic;color:var(--blue);font-size:15px;margin-top:10px}
.arrow{position:absolute;top:1742px;width:31px;height:31px;background:#111;display:flex;align-items:center;justify-content:center}
.arrow svg{width:12px;height:12px;stroke:var(--white);stroke-width:2.5;fill:none}

/* inspired band */
.inspired-band{position:absolute;top:2044px;left:0;width:1200px;height:448px;background:linear-gradient(180deg,#8a6a4c 0%,#6f5540 45%,#4e4a3c 100%);color:var(--white);text-align:center}
.inspired-band h2{position:absolute;top:42px;width:100%;font-size:34px;font-weight:700}
.inspired-band p{position:absolute;top:93px;left:320px;width:560px;font-size:12px;line-height:22px}
.shop-btn{position:absolute;left:542px;top:160px;width:116px;height:32px;border-radius:16px;background:var(--blue);border:2px solid rgba(255,255,255,.7);font-size:11px;font-weight:700;padding-top:7px;text-transform:uppercase}

/* gallery */
.gallery-sub{position:absolute;top:2588px;width:100%;text-align:center;font-size:12px}
.gallery{position:absolute;top:2645px;left:0;width:1200px;height:241px;display:flex}
.gallery div{flex:1}

/* footer */
.site-footer{position:absolute;top:2896px;left:0;width:1200px;height:278px;background:var(--footer)}
.col-rule{position:absolute;top:0;width:1px;height:278px;background:var(--line)}
.footer-title{position:absolute;top:46px;font-size:17px;font-weight:400}
.contact-list{position:absolute;left:98px;top:90px;font-size:12px;color:#444;line-height:20px}
.contact-list li{list-style:none;display:flex;gap:14px;margin-bottom:10px}
.contact-list svg{width:14px;height:14px;fill:#555;flex:none;margin-top:3px}
.quick-links{position:absolute;left:531px;top:88px;list-style:none;font-size:11px;line-height:19.5px;color:#444}
.quick-links li::before{content:"";display:inline-block;border-left:5px solid #444;border-top:3.5px solid transparent;border-bottom:3.5px solid transparent;margin-right:10px}
.news-text{position:absolute;left:791px;top:86px;width:300px;font-size:12px;line-height:20px;color:#444}
.news-field{position:absolute;left:791px;top:140px;width:309px;height:42px;background:var(--white);border:1px solid var(--line);font-size:11px;padding:13px 14px;color:#555}
.news-btn{position:absolute;left:791px;top:191px;width:123px;height:39px;background:var(--blue);color:var(--white);font-size:12px;font-weight:700;text-align:center;padding-top:11px;text-transform:uppercase}

.legal{position:absolute;top:3174px;left:0;width:1200px;height:105px;border-top:1px solid var(--line);text-align:center}
.social{position:absolute;top:24px;left:50%;transform:translateX(-50%);display:flex;gap:6px}
.social i{width:24px;height:24px;border-radius:50%;border:1.5px solid #333}
.legal p{position:absolute;top:64px;width:100%;font-size:11px;color:#555}
</style>
</head>
<body>

<div class="topbar">
  <span class="promo">Free shipping &amp; free returns</span>
  <div class="account">
    <span><svg viewBox="0 0 24 24"><path d="M12 21l-1.5-1.3C5 15 2 12.2 2 8.5 2 5.5 4.4 3 7.5 3c1.7 0 3.4.8 4.5 2.1C13.1 3.8 14.8 3 16.5 3 19.6 3 22 5.5 22 8.5c0 3.7-3 6.5-8.5 11.2z"/></svg>My favorite</span>
    <span><svg viewBox="0 0 24 24"><circle cx="12" cy="7" r="5"/><path d="M2 23c0-6 4.5-9 10-9s10 3 10 9z"/></svg>Sign in</span>
    <span><svg viewBox="0 0 24 24"><path d="M1 2h4l3 12h12l3-9H7"/><circle cx="9" cy="20" r="2"/><circle cx="19" cy="20" r="2"/></svg>0 items</span>
  </div>
</div>

<header class="site-header">
  <div class="brand"><span class="dot"></span>Pup Snack Den</div>
  <nav class="main-nav"><span>Home</span><span>About us</span><span>Get started</span><span>Pup Snack Den</span><span>Contact us</span></nav>
</header>

<section class="hero" role="img" aria-label="Golden puppy eating kibble from a brown bowl on a wooden floor">
  <div class="sale-badge">
    <div class="kicker">PUP SNACK DEN</div>
    <div class="big">SALE</div>
    <div class="sub">UP TO 50% OFF</div>
    <div class="slider-dots"><i></i><i class="on"></i><i class="on"></i></div>
  </div>
</section>

<a class="tile" style="left:98px;background:linear-gradient(135deg,#8c6f55,#b59373 50%,#6e4e3a)" role="img" aria-label="Dog at a picnic with a basket of treats"><span class="label">Sale now on</span></a>
<a class="tile" style="left:437px;background:linear-gradient(135deg,#8a6a4e,#d8cbb8 50%,#7b5a3a)" role="img" aria-label="Two white puppies in chef hats beside baked bread"><span class="label">What's hot</span></a>
<a class="tile" style="left:776px;background:linear-gradient(135deg,#4a3a36,#7e6a64 50%,#3b2e2c)" role="img" aria-label="White kitten beside a blue food bowl"><span class="label">New arrivals</span></a>

<section class="subscribe-band" role="img" aria-label="Dog peering over two food bowls on a wooden floor">
  <h2 class="heading">Pup Snack Den Subscription Box</h2>
  <p>Sed ut perspiciatis unde omnis iste natus error sit voluptatem acctium dolorue laudantium, totam rem aperiam, eaque ipsa quae ab illo invtore veritatis et quasi architecto beatae vitae</p>
  <div class="sub-form"><span class="field">Email</span><span class="btn">Subscription</span></div>
  <div class="gift-box" role="img" aria-label="Kraft paper carry box"></div>
</section>

<h2 class="section-title heading" style="top:1540px">Featured Products</h2>
<div class="arrow" style="left:42px"><svg viewBox="0 0 12 12"><path d="M8 1L3 6l5 5"/></svg></div>
<div class="arrow" style="left:1128px"><svg viewBox="0 0 12 12"><path d="M4 1l5 5-5 5"/></svg></div>

<div class="product" style="left:98px"><div class="shot" role="img" aria-label="Curly dog on a chair behind a plate of kibble" style="background:linear-gradient(180deg,#e3a24a,#c9b9a3 60%,#efe9e0)"></div><p>Sed ut perspiciatis unde omnis iste natus error sit</p><div class="price">$25.99</div></div>
<div class="product" style="left:354px"><div class="shot" role="img" aria-label="Bowl of bone biscuits beside a red heart" style="background:linear-gradient(180deg,#f2c9cc,#f6dcdd 60%,#fbefef)"></div><p>Sed ut perspiciatis unde omnis iste natus error sit</p><div class="price">$25.99</div></div>
<div class="product" style="left:610px"><div class="shot" role="img" aria-label="Packet of dog treats on a teal background" style="background:linear-gradient(180deg,#1f97b4,#1a8aa6)"></div><p>Sed ut perspiciatis unde omnis iste natus error sit</p><div class="price">$25.99</div></div>
<div class="product" style="left:866px"><div class="shot" role="img" aria-label="Illustrated dogs beside a bag of dog food" style="background:linear-gradient(180deg,#fafafa,#eef0f2);border:1px solid #e4e4e4"></div><p>Sed ut perspiciatis unde omnis iste natus error sit</p><div class="price">$25.99</div></div>

<section class="inspired-band" role="img" aria-label="Dog in a green sweater drinking from a pink bowl held by a hand">
  <h2 class="heading">Inspired by dogs</h2>
  <p>Sed ut perspiciatis unde omnis iste natus error sit voluptatem acctium dolorue laudantium, totam rem aperiam, eaque ipsa quae ab illo invtore veritatis et quasi</p>
  <div class="shop-btn">Shop now &#8250;</div>
</section>

<h2 class="section-title heading" style="top:2544px">Pups who ruv it</h2>
<p class="gallery-sub">See why #PupSnackDen drives pups bonkers!</p>
<div class="gallery">
  <div role="img" aria-label="Happy dog in a red scarf with a blue bowl" style="background:linear-gradient(160deg,#d9b48a,#b0702e 60%,#c24a3e)"></div>
  <div role="img" aria-label="Fluffy dog on a lap" style="background:linear-gradient(160deg,#7f6f86,#a79a82 55%,#4f4b57)"></div>
  <div role="img" aria-label="Dog with two bowls of food on a wooden table" style="background:linear-gradient(160deg,#d49a55,#b97637 55%,#e8c7a0)"></div>
  <div role="img" aria-label="Dog by a tray of homemade treats" style="background:linear-gradient(160deg,#b2886a,#8a6549 55%,#d7c2aa)"></div>
  <div role="img" aria-label="Man feeding a treat to a dog" style="background:linear-gradient(160deg,#c24a3e,#d7b79a 55%,#7d5a44)"></div>
</div>

<footer class="site-footer">
  <span class="col-rule" style="left:437px"></span>
  <span class="col-rule" style="left:710px"></span>
  <h3 class="footer-title heading" style="left:98px">Contact us</h3>
  <ul class="contact-list">
    <li><svg viewBox="0 0 24 24"><path d="M12 1a8 8 0 0 0-8 8c0 6 8 14 8 14s8-8 8-14a8 8 0 0 0-8-8zm0 11a3 3 0 1 1 0-6 3 3 0 0 1 0 6z"/></svg><span>Pup Snack Den<br>2280 Maple Ridge Ave, Denver, CO 80211, USA</span></li>
    <li><svg viewBox="0 0 24 24"><path d="M6.6 10.8a15 15 0 0 0 6.6 6.6l2.2-2.2a1 1 0 0 1 1-.25 11.4 11.4 0 0 0 3.6.6 1 1 0 0 1 1 1V20a1 1 0 0 1-1 1A17 17 0 0 1 3 4a1 1 0 0 1 1-1h3.5a1 1 0 0 1 1 1c0 1.25.2 2.45.6 3.6a1 1 0 0 1-.25 1z"/></svg><span>Phone: (555) 014-2739</span></li>
    <li><svg viewBox="0 0 24 24"><path d="M2 5h20v14H2zm2 2v.5l8 5 8-5V7l-8 5z"/></svg><span>Email: info@pupsnackden.com</span></li>
  </ul>
  <h3 class="footer-title heading" style="left:531px">Quick links</h3>
  <ul class="quick-links"><li>Home</li><li>About</li><li>Product</li><li>Category</li><li>Compare Now</li><li>Pricing</li><li>Contact Us</li></ul>
  <h3 class="footer-title heading" style="left:791px">Sign up for newsletter</h3>
  <p class="news-text">Excepteur sint occaecat cupidatat non proident, sunt in culpa qui officia deserunt</p>
  <div class="news-field">Enter email</div>
  <div class="news-btn">Subscription</div>
</footer>

<div class="legal">
  <div class="social"><i></i><i></i><i></i><i></i></div>
  <p>&copy;2017 Pup Snack Den. All Rights Reserved.</p>
</div>

</body>
</html>
```